Quiet Harbor Prints gallery website

I need a Website for a gallery with a shopify integration or maybe even better also compatible with squarespace.
the website should have following riders: Künstler, Veranstaltungen, Shop, About Us.
some nice examples for inspiration of the website architecture are:
https://www.lindwerkraum.com/
https://www.plattenbau-salon.com/de/
https://moorlichtraum.de/
It should be easy for us to make adaptations and fill the website with new content.
Attached there is the CI an logo for the brand.
Target Market(s)
Art Collectors,
Industry/Entity Type
artgallery
Coding
Coded - Design and coding required
Number of Pages Required
3 page
Font styles to use
Look and feel

```html
<!DOCTYPE html>
<html lang="en">
<head>
<meta charset="utf-8">
<title>Quiet Harbor Prints</title>
<link rel="stylesheet" href="https://fonts.googleapis.com/css2?family=Hind:wght@400;600;700&family=Arimo:wght@400;700&display=swap">
<style>
:root{
  --red:#c8102e;
  --black:#000;
  --ink:#0b0b0c;
  --white:#fff;
  --muted:#e6e6e6;
  --band-top:#1c2731;
  --band-bottom:#0e161e;
  --frame:#0a0a0a;
}
*{box-sizing:border-box;margin:0;padding:0}
html,body{width:1200px;height:3430px;overflow:hidden;background:var(--black);color:var(--white);font-family:"Arimo",Arial,sans-serif}
.page{position:relative;width:1200px;height:3430px}
.abs{position:absolute}
.heading{font-family:"Hind",sans-serif;font-weight:700}

/* header */
.site-header{position:absolute;left:0;top:0;width:1200px;height:103px;background:#0d0d0d;z-index:2}
.brand{position:absolute;left:96px;top:38px;display:flex;align-items:center;gap:10px;font-size:17px;letter-spacing:.5px}
.brand .mark{width:12px;height:12px;border:2px solid var(--red)}
.nav{position:absolute;top:38px;left:511px}
.nav a{position:absolute;white-space:nowrap;color:var(--white);text-decoration:none;font-family:"Hind",sans-serif;font-weight:700;font-size:17px}
.nav-icons svg{position:absolute;top:39px}

/* hero */
.hero{position:absolute;left:0;top:103px;width:1200px;height:603px;background:#0e0e10;overflow:hidden}
.hero-art{position:absolute;right:0;top:0;width:760px;height:603px;background:radial-gradient(ellipse at 35% 40%,#8a4a1c 0%,#3a2214 35%,transparent 62%),radial-gradient(ellipse at 68% 40%,#1f6b7a 0%,#16323a 38%,transparent 65%),linear-gradient(90deg,#0e0e10 0%,#15181b 40%,#101418 100%)}
.hero-title{position:absolute;left:94px;top:112px;font-size:60px;line-height:78px}
.hero-text{position:absolute;left:96px;top:280px;width:480px;font-size:16px;line-height:31px;color:var(--muted)}
.btn{position:absolute;display:flex;align-items:center;justify-content:center;border:2px solid var(--red);color:var(--red);font-family:"Hind",sans-serif;font-weight:700;font-size:15px;text-decoration:none}
.dot{position:absolute;width:8px;height:8px;border-radius:50%;background:#9a9a9a}
.dot.active{width:12px;height:12px;background:var(--red)}

/* section heads */
.sq{position:absolute;left:591px;width:18px;height:18px;border:2px solid var(--red)}
.section-title{position:absolute;left:0;width:1200px;text-align:center;font-size:39px;line-height:44px}

.tabs a{position:absolute;top:894px;width:133px;height:43px;border:1.5px solid #cfcfcf;display:flex;align-items:center;justify-content:center;color:var(--white);text-decoration:none;font-size:18px}
.tabs a.active{width:81px;background:var(--red);border-color:var(--red);font-weight:700}

/* gallery */
.gallery-band{position:absolute;left:0;top:982px;width:1200px;height:836px;background:linear-gradient(180deg,#2b2a26 0%,var(--band-top) 18%,var(--band-bottom) 100%)}
.frame{position:absolute;background:var(--frame);padding:9px;box-shadow:0 6px 18px rgba(0,0,0,.6)}
.frame .mat{width:100%;height:100%;background:#f2f2f2;padding:8px}
.frame .art{width:100%;height:100%}

/* events */
.lead{position:absolute;left:0;width:1200px;text-align:center;font-size:16px;line-height:26px;color:var(--muted)}
.event-photo{position:absolute}
.event-title{position:absolute;width:460px;text-align:center;font-size:26px}
.event-text{position:absolute;width:460px;text-align:center;font-size:15px;line-height:31px;color:var(--muted)}

/* newsletter */
.field{position:absolute;top:2889px;height:47px;background:var(--white);color:#111;font-size:13px;padding-left:20px;display:flex;align-items:center}
.subscribe{position:absolute;left:886px;top:2889px;width:169px;height:47px;background:var(--red);color:var(--white);font-family:"Hind",sans-serif;font-weight:700;font-size:16px;display:flex;align-items:center;justify-content:center}
.rule{position:absolute;left:100px;width:1003px;height:1px;background:#555}

/* footer */
.footer-brand{position:absolute;left:97px;top:3154px;display:flex;align-items:center;gap:14px;font-size:27px;letter-spacing:.3px}
.footer-brand .mark{width:18px;height:18px;border:2px solid var(--red)}
.col-title{position:absolute;top:3074px;font-family:"Hind",sans-serif;font-weight:700;font-size:21px}
.links{position:absolute;top:3110px;list-style:none}
.links li{display:flex;align-items:center;gap:12px;height:31px;font-size:15px;color:var(--muted)}
.contact-row{position:absolute;left:836px;display:flex;align-items:center;gap:15px;font-size:15px;color:var(--muted);white-space:nowrap}
.contact-row .ico{width:38px;height:38px;border-radius:50%;background:var(--red);display:flex;align-items:center;justify-content:center;flex:none}
.copyright{position:absolute;left:0;top:3374px;width:1200px;text-align:center;font-size:14px;color:var(--muted)}
</style>
</head>
<body>
<div class="page">

  <header class="site-header">
    <div class="brand"><span class="mark"></span>Quiet Harbor Prints</div>
    <nav class="nav">
      <a style="left:0">Artists</a>
      <a style="left:92px">Events</a>
      <a style="left:183px">Shop</a>
      <a style="left:262px">About Us</a>
      <a style="left:372px">Contact Us</a>
    </nav>
    <div class="nav-icons">
      <svg style="left:1006px" width="20" height="22" viewBox="0 0 20 22" fill="none" stroke="#fff" stroke-width="1.6"><circle cx="10" cy="7" r="5"/><path d="M1 21c1-5 5-7 9-7s8 2 9 7"/></svg>
      <svg style="left:1044px" width="21" height="21" viewBox="0 0 21 21" fill="none" stroke="#fff" stroke-width="1.8"><circle cx="8.5" cy="8.5" r="6.5"/><path d="M13.5 13.5l6 6"/></svg>
      <svg style="left:1083px" width="19" height="23" viewBox="0 0 19 23" fill="none" stroke="#fff" stroke-width="1.6"><rect x="1.5" y="6.5" width="16" height="15"/><path d="M5.5 9V5a4 4 0 0 1 8 0v4"/></svg>
    </div>
  </header>

  <section class="hero">
    <div class="hero-art" role="img" aria-label="Painted portrait artwork in warm orange and teal tones with feathers"></div>
    <h1 class="hero-title heading">Welcome To<br>Quiet Harbor Prints</h1>
    <p class="hero-text">Lorem ipsum dolor sit amet, consectetur adipiscing elit, sed do eiusmod tempor incididunt ut labore et dolore magna aliqua.</p>
    <a class="btn" style="left:96px;top:363px;width:127px;height:48px">Get Started</a>
    <span class="dot active" style="left:102px;top:461px"></span>
    <span class="dot" style="left:125px;top:463px"></span>
    <span class="dot" style="left:145px;top:463px"></span>
    <svg class="abs" style="left:197px;top:462px" width="48" height="10" viewBox="0 0 48 10" fill="none" stroke-width="1.6"><path d="M18 5H2M6 1L2 5l4 4" stroke="#888"/><path d="M26 5h18M40 1l4 4-4 4" stroke="#fff"/></svg>
  </section>

  <span class="sq" style="top:792px"></span>
  <h2 class="section-title heading" style="top:824px">Our Gallery</h2>
  <div class="tabs">
    <a class="active" style="left:253px">All</a>
    <a style="left:352px">Artists</a>
    <a style="left:506px">Events</a>
    <a style="left:661px">Shop</a>
    <a style="left:815px">Fine Arts</a>
  </div>

  <section class="gallery-band">
    <div class="frame" style="left:100px;top:103px;width:322px;height:200px"><div class="mat"><div class="art" role="img" aria-label="Colourful abstract painting of a woman's profile" style="background:linear-gradient(120deg,#e8673c,#2c9aa0 55%,#f0c9a0)"></div></div></div>
    <div class="frame" style="left:437px;top:106px;width:315px;height:397px"><div class="mat"><div class="art" role="img" aria-label="Watercolour painting of a rainbow tree with an elephant" style="background:linear-gradient(180deg,#f4f4f4 15%,#e0b23a 40%,#3a7fbf 58%,#e8e8e8 85%)"></div></div></div>
    <div class="frame" style="left:777px;top:103px;width:324px;height:200px"><div class="mat"><div class="art" role="img" aria-label="Explosive colourful abstract portrait artwork" style="background:radial-gradient(circle at 50% 55%,#2b62c4,#c23b2b 40%,#0c0c16 75%)"></div></div></div>
    <div class="frame" style="left:100px;top:330px;width:312px;height:397px"><div class="mat"><div class="art" role="img" aria-label="Painting of a Paris street with blossom trees and the tower" style="background:linear-gradient(160deg,#a9c6de,#d98fa8 50%,#8a6a4a)"></div></div></div>
    <div class="frame" style="left:437px;top:530px;width:320px;height:197px"><div class="mat"><div class="art" role="img" aria-label="Abstract painting of layered faces in teal and orange" style="background:linear-gradient(90deg,#ede3d2 20%,#1f6f8a 55%,#d9782e)"></div></div></div>
    <div class="frame" style="left:787px;top:330px;width:314px;height:397px"><div class="mat"><div class="art" role="img" aria-label="Folk art painting of a tree with colourful flowers" style="background:linear-gradient(180deg,#f0e6d6,#e2a64a 70%,#f2c84a)"></div></div></div>
  </section>

  <span class="sq" style="top:1909px"></span>
  <h2 class="section-title heading" style="top:1940px">Our Events</h2>
  <p class="lead" style="top:2003px">Lorem ipsum dolor sit amet, consectetur adipiscing elit, sed do eiusmod tempor incididunt ut labore et dolore magna aliqua.</p>

  <div class="event-photo" style="left:107px;top:2095px;width:494px;height:293px;background:linear-gradient(90deg,#3a2c24,#7a5a3a 45%,#d08a2a 70%,#4a4e5a)" role="img" aria-label="Photo of a painter working on a canvas at an easel"></div>
  <h3 class="event-title heading" style="left:640px;top:2126px">Modern Paint</h3>
  <p class="event-text" style="left:640px;top:2178px">Lorem ipsum dolor sit amet, consectetur adipiscing elit, sed do eiusmod tempor incididunt ut labore et dolore magna aliqua. Ut enim ad minim veniam,nisi ut aliquip ex ea commodo consequat.</p>
  <a class="btn" style="left:807px;top:2296px;width:126px;height:48px">View More</a>

  <h3 class="event-title heading" style="left:103px;top:2444px">Group Paint</h3>
  <p class="event-text" style="left:103px;top:2496px">Lorem ipsum dolor sit amet, consectetur adipiscing elit, sed do eiusmod tempor incididunt ut labore et dolore magna aliqua. Ut enim ad minim veniam,nisi ut aliquip ex ea commodo consequat.</p>
  <a class="btn" style="left:270px;top:2615px;width:127px;height:48px">View More</a>
  <div class="event-photo" style="left:603px;top:2392px;width:495px;height:293px;background:linear-gradient(120deg,#2a1e18,#8a4a2a 40%,#c47a3a 65%,#3a2a22)" role="img" aria-label="Photo of people painting together at a workshop table"></div>

  <span class="sq" style="top:2766px"></span>
  <h2 class="section-title heading" style="top:2806px;font-size:35px">Sign Up To The Newsletter today</h2>
  <div class="field" style="left:145px;width:352px">NAME</div>
  <div class="field" style="left:514px;width:352px">EMAIL</div>
  <div class="subscribe">SUBSCRIBE</div>

  <div class="rule" style="top:2996px"></div>

  <footer>
    <div class="footer-brand"><span class="mark"></span>Quiet Harbor Prints</div>

    <h4 class="col-title" style="left:437px">Quick Links</h4>
    <ul class="links" style="left:439px">
      <li><svg width="14" height="12" viewBox="0 0 14 12" fill="#fff"><path d="M0 4.5h8V0l6 6-6 6V7.5H0z"/></svg>Artists</li>
      <li><svg width="14" height="12" viewBox="0 0 14 12" fill="#fff"><path d="M0 4.5h8V0l6 6-6 6V7.5H0z"/></svg>Events</li>
      <li><svg width="14" height="12" viewBox="0 0 14 12" fill="#fff"><path d="M0 4.5h8V0l6 6-6 6V7.5H0z"/></svg>Shop</li>
      <li><svg width="14" height="12" viewBox="0 0 14 12" fill="#fff"><path d="M0 4.5h8V0l6 6-6 6V7.5H0z"/></svg>About Us</li>
      <li><svg width="14" height="12" viewBox="0 0 14 12" fill="#fff"><path d="M0 4.5h8V0l6 6-6 6V7.5H0z"/></svg>Contact Us</li>
    </ul>

    <h4 class="col-title" style="left:635px">Other Links</h4>
    <ul class="links" style="left:636px">
      <li><svg width="14" height="12" viewBox="0 0 14 12" fill="#fff"><path d="M0 4.5h8V0l6 6-6 6V7.5H0z"/></svg>FAQ</li>
      <li><svg width="14" height="12" viewBox="0 0 14 12" fill="#fff"><path d="M0 4.5h8V0l6 6-6 6V7.5H0z"/></svg>Tems of Use</li>
      <li><svg width="14" height="12" viewBox="0 0 14 12" fill="#fff"><path d="M0 4.5h8V0l6 6-6 6V7.5H0z"/></svg>Privacy Policy</li>
      <li><svg width="14" height="12" viewBox="0 0 14 12" fill="#fff"><path d="M0 4.5h8V0l6 6-6 6V7.5H0z"/></svg>Support Links</li>
      <li><svg width="14" height="12" viewBox="0 0 14 12" fill="#fff"><path d="M0 4.5h8V0l6 6-6 6V7.5H0z"/></svg>Conditions</li>
    </ul>

    <h4 class="col-title" style="left:836px">Contact Us</h4>
    <div class="contact-row" style="top:3120px"><span class="ico"><svg width="12" height="16" viewBox="0 0 12 16" fill="#fff"><path d="M6 0a6 6 0 0 0-6 6c0 4.5 6 10 6 10s6-5.5 6-10a6 6 0 0 0-6-6zm0 8.3A2.3 2.3 0 1 1 6 3.7a2.3 2.3 0 0 1 0 4.6z"/></svg></span>Quiet Harbor Prints, Harbor Ln 12</div>
    <div class="contact-row" style="top:3179px"><span class="ico"><svg width="14" height="11" viewBox="0 0 14 11" fill="#fff"><path d="M0 0h14v1.5L7 6 0 1.5z"/><path d="M0 3.2l7 4.5 7-4.5V11H0z"/></svg></span>info@quietharborprints.com</div>
    <div class="contact-row" style="top:3239px"><span class="ico"><svg width="14" height="14" viewBox="0 0 14 14" fill="#fff"><path d="M3 0l2.5 3.2-1.3 1.9a8 8 0 0 0 4.7 4.7l1.9-1.3L14 11l-1.5 2.5C6 14 0 8 .5 1.5z"/></svg></span>+1 555 0142 7788</div>

    <div class="rule" style="top:3340px;background:#777"></div>
    <p class="copyright">Copyrights@2024.Quiet Harbor Prints.All Rights Reserved</p>
  </footer>

</div>
</body>
</html>
```